A website for a Maltese Law Firm

Our law firm needs a website to further its business. The site should have a simple yet effective design. We would need the following sections: About us, Practice Areas, About Malta, Contact. These should be further split as follows:

About us: Our firm, Our values, What others say, Offices

Practice Areas: Crimimal, Citizenship & Residence, Sovereign Patron Pathway, Criminal Defence, Civil Litigation, Arbitration and ADR, Commercial and Corporate, Media Law.

About Malta: just one section.

Contact: Just one section

We would also need a news feed at the front of the site to include latest news regarding our cases.

At the bottom we need a section for our Terms and a Privacy Statement.

Our logo is being attached.

Target Market(s)

All clients looking for legal assistance in Malta

Industry/Entity Type

Legal

Coding

Coded - Design and coding required

Number of Pages Required

1 page

Requirements
Must have
• It must be simple yet striking.

```html
<!DOCTYPE html>
<html lang="en">
<head>
<meta charset="utf-8">
<title>Borg &amp; Micallef Advocates</title>
<link href="https://fonts.googleapis.com/css2?family=Montserrat:wght@300;400;500;600&display=swap" rel="stylesheet">
<style>
:root{
  --ink:#222222;
  --text:#444444;
  --muted:#666666;
  --white:#ffffff;
  --hero-dark:#1c1a17;
  --hero-mid:#3a3326;
  --button-tan:#6e6659;
  --panel-grey:#f7f7f7;
  --band-grey:#e9ebe6;
  --button-dark:#2a2a2a;
  --rule:#cfcfcf;
  --input-bg:#eeeeeb;
}
*{margin:0;padding:0;box-sizing:border-box}
html,body{width:696px;height:1200px;overflow:hidden;background:var(--white)}
body{position:relative;font-family:'Montserrat',sans-serif;color:var(--text)}
.abs{position:absolute}

/* hero */
.hero{left:0;top:0;width:696px;height:306px;background:linear-gradient(115deg,var(--hero-dark) 0%,var(--hero-mid) 45%,#221f1a 100%)}
.hero-portrait{left:407px;top:51px;width:189px;height:255px;background:linear-gradient(180deg,#5a5249 0%,#2b2927 60%,#1d1c1b 100%);border-radius:90px 90px 0 0}
.brand{left:103px;top:12px;color:var(--white);font-size:12px;font-weight:500;letter-spacing:.5px;line-height:14px}
.header-divider{left:216px;top:13px;width:1px;height:14px;background:rgba(255,255,255,.35)}
.header-phone{left:228px;top:14px;color:var(--white);font-size:7.5px;font-weight:500;display:flex;align-items:center;gap:4px}
.main-nav{right:127px;top:15px;display:flex;gap:8px;font-size:6.5px;font-weight:500;color:var(--white);white-space:nowrap}
.search-icon{left:581px;top:13px}
.header-rule{left:103px;top:39px;width:490px;height:1px;background:rgba(255,255,255,.25)}
.hero-title{left:103px;top:138px;color:var(--white);font-size:19px;font-weight:500;letter-spacing:.2px}
.hero-sub{left:103px;top:159px;color:var(--white);font-size:8.2px;font-weight:500}
.hero-button{left:103px;top:178px;width:86px;height:23px;background:var(--button-tan);color:var(--white);font-size:7px;font-weight:500;display:flex;align-items:center;justify-content:center}

/* section heads */
.section-title{left:0;width:696px;text-align:center;color:var(--ink);font-size:15px;font-weight:400;letter-spacing:.3px}
.section-rule{left:333px;width:30px;height:1px;background:#bbbbbb}
.section-intro{left:0;width:696px;text-align:center;font-size:7.3px;line-height:9.5px;color:var(--text)}

/* practice areas */
.practice{width:130px;text-align:center}
.practice svg{display:block;margin:0 auto}
.practice-name{color:var(--ink);font-size:7.8px;margin-top:6px}
.practice-text{font-size:7.1px;line-height:9.5px;margin-top:6px;color:var(--text)}

/* news */
.news-panel{left:0;top:665px;width:696px;height:302px;background:var(--panel-grey)}
.news-card{width:126px}
.news-photo{width:126px;height:87px;background:linear-gradient(135deg,#8c8274 0%,#b9b1a5 50%,#4e4b47 100%)}
.news-title{font-size:7.8px;line-height:12px;color:var(--ink);margin-top:8px;height:24px}
.news-rule{height:1px;background:#999;margin-top:5px}
.news-meta{display:flex;gap:9px;font-size:5.8px;color:var(--muted);margin-top:6px;align-items:center}
.news-meta span{display:flex;align-items:center;gap:3px}

/* cta */
.cta-band{left:0;top:967px;width:696px;height:92px;background:linear-gradient(90deg,#e4e7e1 0%,#eff0ec 50%,#e3e5df 100%)}
.cta-title{left:189px;top:1002px;color:var(--ink);font-size:13px;font-weight:400}
.cta-sub{left:189px;top:1017px;font-size:7.2px;color:var(--text)}
.cta-button{left:452px;top:1002px;width:86px;height:22px;background:var(--button-dark);color:var(--white);font-size:6.8px;font-weight:500;display:flex;align-items:center;justify-content:center}

/* footer */
.footer-col{font-size:6.4px;line-height:13px;color:var(--text)}
.footer-head{color:var(--ink);font-size:6.6px}
.newsletter-text{width:120px;line-height:9px;margin-top:2px}
.newsletter-input{left:480px;top:1122px;width:111px;height:16px;background:var(--input-bg);font-size:6.2px;display:flex;align-items:center;justify-content:space-between;padding:0 7px}
.footer-rule{left:103px;top:1169px;width:490px;height:1px;background:#e4e4e4}
.copyright{left:0;top:1181px;width:696px;text-align:center;font-size:6px;color:var(--text)}
</style>
</head>
<body>

<!-- hero -->
<div class="abs hero" role="img" aria-label="Dark photograph of office towers seen from below"></div>
<div class="abs hero-portrait" role="img" aria-label="Portrait of a smiling lawyer in a dark suit with arms crossed"></div>
<div class="abs brand">Borg &amp; Micallef</div>
<div class="abs header-divider"></div>
<div class="abs header-phone">
  <svg width="7" height="7" viewBox="0 0 10 10"><path d="M2 1l2 2-1 1.2c.6 1.3 1.5 2.2 2.8 2.8L7 6l2 2-1.3 1.3C4.5 9 1 5.5.7 2.3z" fill="#fff"/></svg>
  (356) 2000 1234
</div>
<nav class="abs main-nav"><span>HOME</span><span>ABOUT US</span><span>NEWS</span><span>ABOUT MALTA</span><span>CONTACT US</span></nav>
<svg class="abs search-icon" width="11" height="11" viewBox="0 0 12 12"><circle cx="5" cy="5" r="3.8" fill="none" stroke="#fff" stroke-width="1"/><line x1="7.8" y1="7.8" x2="11" y2="11" stroke="#fff" stroke-width="1"/></svg>
<div class="abs header-rule"></div>
<h1 class="abs hero-title">CORPORATE AND COMMERCIAL</h1>
<p class="abs hero-sub">Commission proposes Amendments to Shareholders' Rights Directive</p>
<div class="abs hero-button">LEARN MORE</div>

<!-- practice areas -->
<h2 class="abs section-title" style="top:347px">PRACTICE AREAS</h2>
<div class="abs section-rule" style="top:373px"></div>
<p class="abs section-intro" style="top:380px">Lorem ipsum dolor sit amet, consectetur adipiscing elit.<br>Integer posuere erat a ante venenatis dapibus posuere velit aliquet.</p>

<div class="abs practice" style="left:89px;top:427px">
  <svg width="30" height="28" viewBox="0 0 30 28" fill="none" stroke="#222" stroke-width="1.2"><circle cx="8" cy="20" r="5"/><circle cx="22" cy="20" r="5"/><circle cx="8" cy="20" r="2.5"/><circle cx="22" cy="20" r="2.5"/><circle cx="9" cy="10" r="1.6"/><circle cx="12" cy="5" r="1.6"/><circle cx="18" cy="5" r="1.6"/><circle cx="21" cy="10" r="1.6"/></svg>
  <div class="practice-name">Crimimal</div>
  <div class="practice-text">Lorem ipsum dolor sit amet,<br>consectetur adipiscing elit.<br>Integer posuere erat.</div>
</div>
<div class="abs practice" style="left:217px;top:427px">
  <svg width="30" height="28" viewBox="0 0 30 28" fill="none" stroke="#222" stroke-width="1.2"><rect x="6" y="2" width="16" height="24" rx="1"/><line x1="9" y1="2" x2="9" y2="26"/><circle cx="15.5" cy="12" r="4"/><line x1="11.5" y1="12" x2="19.5" y2="12"/><line x1="12" y1="20" x2="19" y2="20"/><path d="M22 6l4 2-3 18"/></svg>
  <div class="practice-name">Citizenship &amp; Residence</div>
  <div class="practice-text">Lorem ipsum dolor sit amet,<br>consectetur adipiscing elit.<br>Integer posuere erat.</div>
</div>
<div class="abs practice" style="left:346px;top:427px">
  <svg width="30" height="28" viewBox="0 0 30 28" fill="none" stroke="#222" stroke-width="1.2"><path d="M2 8l6-4 5 3 4-2 5 3 6-2"/><path d="M2 8l4 9 8 7c1 1 3 0 2-2"/><path d="M28 6l-3 10-6 6c-1 1-3 0-2-1"/><path d="M17 5l-5 5c-1 1 0 3 2 2l4-3 7 7"/><path d="M10 19l3 3M13 16l4 4"/></svg>
  <div class="practice-name">Sovereign Patron Pathway</div>
  <div class="practice-text">Lorem ipsum dolor sit amet,<br>consectetur adipiscing elit.<br>Integer posuere erat.</div>
</div>
<div class="abs practice" style="left:466px;top:427px">
  <svg width="30" height="28" viewBox="0 0 30 28" fill="none" stroke="#222" stroke-width="1.2"><line x1="15" y1="2" x2="15" y2="24"/><line x1="5" y1="6" x2="25" y2="6"/><path d="M5 6l-3 9h6z"/><path d="M25 6l-3 9h6z"/><path d="M2 15a3 2 0 0 0 6 0M22 15a3 2 0 0 0 6 0"/><rect x="8" y="24" width="14" height="2"/></svg>
  <div class="practice-name">Criminal Defence</div>
  <div class="practice-text">Lorem ipsum dolor sit amet,<br>consectetur adipiscing elit.<br>Integer posuere erat.</div>
</div>

<div class="abs practice" style="left:89px;top:537px">
  <svg width="30" height="28" viewBox="0 0 30 28" fill="none" stroke="#222" stroke-width="1.2"><circle cx="9" cy="5" r="2.2"/><circle cx="15" cy="5" r="2.2"/><circle cx="21" cy="5" r="2.2"/><path d="M5 12c0-3 8-3 8 0M11 12c0-3 8-3 8 0M17 12c0-3 8-3 8 0"/><rect x="3" y="12" width="24" height="14"/><line x1="3" y1="16" x2="27" y2="16"/><line x1="11" y1="16" x2="11" y2="26"/><line x1="19" y1="16" x2="19" y2="26"/></svg>
  <div class="practice-name">Civil Litigation</div>
  <div class="practice-text">Lorem ipsum dolor sit amet,<br>consectetur adipiscing elit.<br>Integer posuere erat.</div>
</div>
<div class="abs practice" style="left:217px;top:537px">
  <svg width="30" height="28" viewBox="0 0 30 28" fill="none" stroke="#222" stroke-width="1.2"><rect x="12" y="2" width="8" height="12" rx="1" transform="rotate(45 16 8)"/><line x1="13" y1="11" x2="5" y2="19"/><rect x="14" y="22" width="12" height="3"/><line x1="12" y1="25" x2="28" y2="25"/></svg>
  <div class="practice-name">Arbitration and ADR</div>
  <div class="practice-text">Lorem ipsum dolor sit amet,<br>consectetur adipiscing elit.<br>Integer posuere erat.</div>
</div>
<div class="abs practice" style="left:346px;top:537px">
  <svg width="30" height="28" viewBox="0 0 30 28" fill="none" stroke="#222" stroke-width="1.2"><path d="M4 3h22l2 7H2z"/><path d="M2 10a3.25 3 0 0 0 6.5 0a3.25 3 0 0 0 6.5 0a3.25 3 0 0 0 6.5 0a3.25 3 0 0 0 6.5 0"/><line x1="8" y1="3" x2="7" y2="10"/><line x1="15" y1="3" x2="15" y2="10"/><line x1="22" y1="3" x2="23" y2="10"/><rect x="4" y="13" width="22" height="13"/><line x1="4" y1="22" x2="26" y2="22"/></svg>
  <div class="practice-name">Commercial and Corporate</div>
  <div class="practice-text">Lorem ipsum dolor sit amet,<br>consectetur adipiscing elit.<br>Integer posuere erat.</div>
</div>
<div class="abs practice" style="left:466px;top:537px">
  <svg width="30" height="28" viewBox="0 0 30 28" fill="none" stroke="#222" stroke-width="1.2"><circle cx="15" cy="14" r="12"/><path d="M19 10a5.5 5.5 0 1 0 0 8"/></svg>
  <div class="practice-name">Media Law</div>
  <div class="practice-text">Lorem ipsum dolor sit amet,<br>consectetur adipiscing elit.<br>Integer posuere erat.</div>
</div>

<!-- latest news -->
<div class="abs news-panel"></div>
<h2 class="abs section-title" style="top:698px">LATEST NEWS</h2>
<div class="abs section-rule" style="top:724px"></div>
<p class="abs section-intro" style="top:731px">Lorem ipsum dolor sit amet, consectetur adipiscing elit.<br>Integer posuere erat a ante venenatis dapibus posuere velit aliquet.</p>

<article class="abs news-card" style="left:101px;top:782px">
  <div class="news-photo" role="img" aria-label="Photo of colleagues listening in a meeting"></div>
  <div class="news-title">Lorem ipsum dolor sit amet,<br>consectetur</div>
  <div class="news-rule"></div>
  <div class="news-meta">
    <span><svg width="6" height="6" viewBox="0 0 6 6"><circle cx="3" cy="1.7" r="1.5" fill="#666"/><path d="M0 6c0-2 6-2 6 0z" fill="#666"/></svg>John Doe</span>
    <span><svg width="7" height="6" viewBox="0 0 7 6"><path d="M1 0h5a1 1 0 0 1 1 1v2.5a1 1 0 0 1-1 1H3L1 6V4.5a1 1 0 0 1-1-1V1a1 1 0 0 1 1-1z" fill="#666"/></svg>80</span>
    <span><svg width="8" height="5" viewBox="0 0 8 5"><path d="M0 2.5C2-.8 6-.8 8 2.5 6 5.8 2 5.8 0 2.5z" fill="#666"/><circle cx="4" cy="2.5" r="1" fill="#f7f7f7"/></svg>456</span>
  </div>
</article>
<article class="abs news-card" style="left:284px;top:782px">
  <div class="news-photo" role="img" aria-label="Photo of a team reviewing documents at a table"></div>
  <div class="news-title">Lorem ipsum dolor sit amet,<br>consectetur</div>
  <div class="news-rule"></div>
  <div class="news-meta">
    <span><svg width="6" height="6" viewBox="0 0 6 6"><circle cx="3" cy="1.7" r="1.5" fill="#666"/><path d="M0 6c0-2 6-2 6 0z" fill="#666"/></svg>John Doe</span>
    <span><svg width="7" height="6" viewBox="0 0 7 6"><path d="M1 0h5a1 1 0 0 1 1 1v2.5a1 1 0 0 1-1 1H3L1 6V4.5a1 1 0 0 1-1-1V1a1 1 0 0 1 1-1z" fill="#666"/></svg>80</span>
    <span><svg width="8" height="5" viewBox="0 0 8 5"><path d="M0 2.5C2-.8 6-.8 8 2.5 6 5.8 2 5.8 0 2.5z" fill="#666"/><circle cx="4" cy="2.5" r="1" fill="#f7f7f7"/></svg>456</span>
  </div>
</article>
<article class="abs news-card" style="left:464px;top:782px">
  <div class="news-photo" role="img" aria-label="Photo of business people shaking hands outdoors"></div>
  <div class="news-title">Lorem ipsum dolor sit amet,<br>consectetur</div>
  <div class="news-rule"></div>
  <div class="news-meta">
    <span><svg width="6" height="6" viewBox="0 0 6 6"><circle cx="3" cy="1.7" r="1.5" fill="#666"/><path d="M0 6c0-2 6-2 6 0z" fill="#666"/></svg>John Doe</span>
    <span><svg width="7" height="6" viewBox="0 0 7 6"><path d="M1 0h5a1 1 0 0 1 1 1v2.5a1 1 0 0 1-1 1H3L1 6V4.5a1 1 0 0 1-1-1V1a1 1 0 0 1 1-1z" fill="#666"/></svg>80</span>
    <span><svg width="8" height="5" viewBox="0 0 8 5"><path d="M0 2.5C2-.8 6-.8 8 2.5 6 5.8 2 5.8 0 2.5z" fill="#666"/><circle cx="4" cy="2.5" r="1" fill="#f7f7f7"/></svg>456</span>
  </div>
</article>

<!-- terms band -->
<div class="abs cta-band" role="img" aria-label="Faded photo of a desk with documents"></div>
<h2 class="abs cta-title">TERMS AND A PRIVACY STATEMENT</h2>
<p class="abs cta-sub">Lorem ipsum dolor sit amet, consectetur adipiscing elit.</p>
<div class="abs cta-button">GET STARTED</div>

<!-- footer -->
<div class="abs footer-col" style="left:103px;top:1082px">
  <div class="footer-head">CONTACT</div>
  <div>Email: info@borgmicallef.example</div>
  <div>12/4, Harbour Lane, Valletta</div>
  <div>58, Orchard Street, Birkirkara</div>
  <div>(356) 2000 5678</div>
  <div>(356) 2000 9012</div>
</div>
<div class="abs footer-col" style="left:254px;top:1082px">
  <div>Home</div><div>About Us</div><div>News</div><div>About Malta</div><div>Contact Us</div>
</div>
<div class="abs footer-col" style="left:363px;top:1082px">
  <div>Support</div><div>Resources</div><div>F.A.Q.</div>
</div>
<div class="abs footer-col" style="left:480px;top:1082px">
  <div class="footer-head">NEWSLETTER</div>
  <div class="newsletter-text">Subscribe to our newsletter and get all the cool news</div>
</div>
<div class="abs newsletter-input">
  <span>Enter Email</span>
  <svg width="8" height="8" viewBox="0 0 8 8"><path d="M0 3.5L8 0 5 8 4 4.5z" fill="none" stroke="#333" stroke-width=".8"/></svg>
</div>
<div class="abs footer-rule"></div>
<p class="abs copyright">©2016 · Borg and Micallef advocates.</p>

</body>
</html>
```